Pet sitting Business needs a website

We need a website that shows our services and prices. Shows our love of animals but also our professionalism. want a gallery, about, blog, services, links to fb and instagram accounts, newsletter archive. want it to be easy to access and wonderful to navigate. want the domain to be Birchfordpawhaven.com
take any info from FB site www.facebook.com/birchfordpawhaven
I would like it to fit square space platform

Target Market(s)

upscale area, responsible pet owners,

Industry/Entity Type

Pet Care

Coding

Coded - Design and coding required

Number of Pages Required

5+ page

Font styles to use
Sans Serif

Requirements
Must have
• (square space platform)
• Menu
• photo gallery
• about us
• services
• policies
• monthly newsletter
• unavailable dates
• Introduction (welcome)
• payment methods
• Daily updates
• testimonials (use from fb site)
Should not have
• stock photos

```html
<!DOCTYPE html>
<html lang="en">
<head>
<meta charset="utf-8">
<title>Birchford Paw Haven – Petsitting Club</title>
<link href="https://fonts.googleapis.com/css2?family=Roboto:wght@300;400;500;700&display=swap" rel="stylesheet">
<style>
:root{
  --blue:#1a8fc1;
  --blue-dark:#0f76a3;
  --gold:#e09a00;
  --gold-soft:#f0b43a;
  --ink:#222;
  --muted:#666;
  --light:#f1f1f1;
  --footer:#2b2b2b;
  --footer-deep:#1e1e1e;
  --white:#fff;
}
*{margin:0;padding:0;box-sizing:border-box}
html,body{width:1200px;height:2866px;overflow:hidden}
body{font-family:'Roboto',Arial,sans-serif;color:var(--ink);background:var(--white);position:relative}
.abs{position:absolute}
.topline{left:0;top:0;width:1200px;height:5px;background:linear-gradient(90deg,var(--blue-dark),var(--gold),var(--blue-dark))}
.header{left:0;top:5px;width:1200px;height:148px;background:var(--white)}
.contact-line{top:64px;font-size:13px;color:var(--muted);display:flex;align-items:center;gap:8px}
.contact-line svg{width:14px;height:14px}
.brand{left:460px;top:40px;width:280px;text-align:center}
.brand-mark{width:34px;height:34px;border-radius:50%;background:var(--gold);margin:0 auto 8px}
.brand-name{font-size:27px;font-weight:500;color:var(--gold);line-height:1}
.socials{right:100px;top:60px;display:flex;gap:18px}
.socials span{width:38px;height:38px;border:1.5px solid #444;border-radius:50%;display:block}
.nav{left:0;top:153px;width:1200px;height:53px;background:linear-gradient(var(--blue),var(--blue-dark));display:flex;padding-left:97px}
.nav a{color:var(--white);text-decoration:none;font-size:14.5px;line-height:53px;padding:0 16px}
.nav a.active{background:var(--gold);padding:0 27px}
.hero{left:0;top:206px;width:1200px;height:497px;background:linear-gradient(100deg,#e9ecef 0%,#d9dde0 40%,#7c6a55 70%,#c9c4bd 100%)}
.hero-title{left:97px;top:345px;font-size:42px;font-weight:700;letter-spacing:.5px}
.hero-title .gold{color:var(--gold)} .hero-title .blue{color:var(--blue)}
.hero-sub{left:97px;top:405px;font-size:26px;font-weight:300;color:#333}
.btn-blue{left:97px;top:480px;width:129px;height:42px;background:var(--blue);color:var(--white);font-size:16px;text-align:center;line-height:42px;border-radius:2px}
.arrow{top:440px;width:34px;height:34px;border-radius:50%;background:rgba(255,255,255,.35)}
.service{width:262px;text-align:center;top:642px}
.service .crop{width:216px;height:162px;margin:0 auto;overflow:hidden}
.service .photo{width:206px;height:206px;border-radius:50%;border:5px solid var(--white);margin:0 auto}
.service h3{font-size:21px;font-weight:500;margin-top:18px;line-height:26px}
.service .price{font-size:25px;font-weight:700;color:var(--gold);margin-top:6px;line-height:30px}
.service .price small{font-size:10px;font-weight:400}
.service p{font-size:12px;color:var(--muted);line-height:23px;margin-top:4px}
.service .more{color:var(--gold);font-size:13px;margin-top:10px}
.why{left:0;top:1007px;width:1200px;height:526px;background:var(--light)}
.sec-title{width:1200px;left:0;text-align:center;font-size:27px;font-weight:700}
.sec-rule{left:578px;width:44px;height:2px;background:var(--blue)}
.why-intro{left:230px;top:1122px;width:740px;text-align:center;font-size:12px;color:var(--muted);line-height:23px}
.feature{width:320px;text-align:center;top:1195px}
.feature .icon{width:122px;height:122px;border-radius:50%;background:var(--gold);margin:0 auto;display:flex;align-items:center;justify-content:center}
.feature h4{font-size:17px;font-weight:500;margin-top:30px}
.feature p{font-size:12px;color:var(--muted);line-height:21px;margin-top:10px}
.btn-gold{display:inline-block;width:96px;height:34px;line-height:34px;background:var(--gold);color:var(--white);font-size:13px;font-weight:500;margin-top:14px}
.gallery{left:0;top:1533px;width:1200px;height:525px;display:grid;grid-template-columns:repeat(4,1fr);grid-template-rows:repeat(2,1fr);gap:2px;background:var(--white)}
.gallery div{width:100%;height:100%}
.quote-avatar{width:77px;height:77px;border-radius:50%;background:linear-gradient(#d9c8b8,#9a8572);border:3px solid #ddd}
.quote{width:369px;height:172px;border:2px solid var(--gold);background:var(--white)}
.quote p{padding:14px 20px 0;font-size:12px;color:var(--muted);line-height:21px}
.quote .who{position:absolute;left:0;bottom:0;width:100%;height:63px;background:var(--gold);color:var(--white);padding:12px 20px}
.quote .who b{font-size:13px;font-weight:500;display:block}
.quote .who span{font-size:11px}
.sub-band{left:0;top:2427px;width:1200px;height:101px;background:var(--footer-deep)}
.sub-blue{left:0;top:2427px}
.sub-text{left:191px;top:2448px;color:var(--white);font-size:21px;font-weight:500;line-height:28px}
.sub-text b{font-size:25px;font-weight:500}
.sub-input{left:678px;top:2465px;width:289px;height:38px;background:var(--white);font-size:12px;color:#555;line-height:38px;padding-left:42px}
.sub-btn{left:967px;top:2465px;width:132px;height:38px;background:var(--gold);color:var(--white);font-size:14px;text-align:center;line-height:38px}
.footer{left:0;top:2528px;width:1200px;height:272px;background:var(--footer)}
.fcol{top:2585px;color:#bbb;font-size:11.5px}
.fcol h5{color:var(--white);font-size:16px;font-weight:500;margin-bottom:18px}
.fcol li{list-style:none;line-height:26px}
.fcol li::before{content:"› ";color:#999}
.fcol.plain li::before{content:""}
.fcol.contact li::before{content:""}
.fcol.contact svg{width:11px;height:11px;vertical-align:-1px;margin-right:8px}
.bottom{left:0;top:2800px;width:1200px;height:66px;background:#1a1a1a;color:#ccc;font-size:11.5px;text-align:center;line-height:66px}
</style>
</head>
<body>
<div class="abs topline"></div>
<header class="abs header"></header>
<div class="abs contact-line" style="left:97px">
  <svg viewBox="0 0 16 16"><path d="M4 1l3 3-2 2c1 2 3 4 5 5l2-2 3 3-2 3C7 15 1 9 1 3z" fill="var(--blue)"/></svg>
  <span>+789 5550142210</span>
  <svg viewBox="0 0 16 16" style="margin-left:26px"><rect x="1" y="3" width="14" height="10" fill="none" stroke="var(--blue)" stroke-width="1.5"/><path d="M1 3l7 6 7-6" fill="none" stroke="var(--blue)" stroke-width="1.5"/></svg>
  <span>info@birchfordpawhaven.com</span>
</div>
<div class="abs brand"><div class="brand-mark"></div><div class="brand-name">Birchford Paw Haven</div></div>
<div class="abs socials" aria-label="Social links"><span></span><span></span><span></span><span></span></div>

<nav class="abs nav">
  <a class="active">Home</a><a>About us</a><a>Services</a><a>Photo gallery</a><a>Policies</a><a>Monthly newsletter</a><a>Unavailable dates</a><a>Payment methods</a><a>Contact us</a>
</nav>

<section class="abs hero" role="img" aria-label="Photo of a happy puppy lying beside a tabby cat on a white floor"></section>
<div class="abs arrow" style="left:24px"></div>
<div class="abs arrow" style="right:24px"></div>
<h1 class="abs hero-title"><span class="gold">WE ARE </span><span class="blue">BIRCHFORD</span></h1>
<div class="abs hero-sub">Petsitting Club headed by Vet Tech Nora Vale</div>
<div class="abs btn-blue">Learn More</div>

<div class="abs service" style="left:73px"><div class="crop"><div class="photo" role="img" aria-label="Photo of a dog on a visit in the garden" style="background:linear-gradient(#5f7a3e,#9fae7c)"></div></div><h3>Daily Visit</h3><div class="price">$25.00 <small>/ (per visit)</small></div><p>No additional charge for each pet<br>Dog walks or play time</p><div class="more">Read More</div></div>
<div class="abs service" style="left:335px"><div class="crop"><div class="photo" role="img" aria-label="Photo of a cat on a porch" style="background:linear-gradient(#3a2a3a,#c9bfc4)"></div></div><h3>Potty visits</h3><div class="price">$10.00 <small>/ (per visit)</small></div><p>No additional charge for each pet<br>Dog walks or play time</p><div class="more">Read More</div></div>
<div class="abs service" style="left:597px"><div class="crop"><div class="photo" role="img" aria-label="Photo of a pet in a travel crate" style="background:linear-gradient(#3b2a1e,#7a5a3c)"></div></div><h3>Pet Taxi</h3><div class="price">$10.00 <small>/ (each trip)</small></div><p>No additional charge for each pet<br>Dog walks or play time</p><div class="more">Read More</div></div>
<div class="abs service" style="left:861px"><div class="crop"><div class="photo" role="img" aria-label="Photo of a cat beside a food bowl" style="background:linear-gradient(#8a7a68,#4e6f78)"></div></div><h3>Medication</h3><div class="price">$5.00 <small>/ (per Admistion)</small></div><p>No additional charge for each pet<br>Dog walks or play time</p><div class="more">Read More</div></div>

<section class="abs why"></section>
<h2 class="abs sec-title" style="top:1052px">Why Choose Us</h2>
<div class="abs sec-rule" style="top:1101px"></div>
<p class="abs why-intro">It is a long established fact that a reader will be distracted by the readable content of a page when looking at its layout. The point of using Lorem Ipsum is that it has a more-or-less normal distribution of letters, as opposed to using 'Content here, content here</p>
<div class="abs feature" style="left:117px"><div class="icon"><svg width="60" height="60" viewBox="0 0 60 60"><rect x="14" y="24" width="30" height="12" rx="5" fill="#fff"/><rect x="16" y="34" width="4" height="16" fill="#fff"/><rect x="38" y="34" width="4" height="16" fill="#fff"/><circle cx="44" cy="18" r="7" fill="#fff"/></svg></div><h4>Finibus Bonorum et</h4><p>The standard chunk of Lorem Ipsum used since the<br>is reproduced below for those interested.</p><div class="btn-gold">Read More</div></div>
<div class="abs feature" style="left:438px"><div class="icon"><svg width="60" height="60" viewBox="0 0 60 60"><circle cx="22" cy="22" r="7" fill="#fff"/><rect x="14" y="29" width="16" height="20" rx="6" fill="#fff"/><circle cx="40" cy="30" r="6" fill="#fff"/><rect x="33" y="36" width="14" height="13" rx="5" fill="#fff"/></svg></div><h4>Finibus Bonorum et</h4><p>The standard chunk of Lorem Ipsum used since the<br>is reproduced below for those interested.</p><div class="btn-gold">Read More</div></div>
<div class="abs feature" style="left:763px"><div class="icon"><svg width="60" height="60" viewBox="0 0 60 60"><circle cx="30" cy="24" r="15" fill="none" stroke="#fff" stroke-width="4"/><path d="M22 37l-4 16 12-6 12 6-4-16" fill="#fff"/><circle cx="30" cy="26" r="4" fill="#fff"/></svg></div><h4>Finibus Bonorum et</h4><p>The standard chunk of Lorem Ipsum used since the<br>is reproduced below for those interested.</p><div class="btn-gold">Read More</div></div>

<section class="abs gallery">
  <div role="img" aria-label="Photo of tortoises on leaves" style="background:linear-gradient(#5a4a3a,#8a7a5a)"></div>
  <div role="img" aria-label="Photo of a girl holding a pug" style="background:linear-gradient(#4f6b3a,#8a9a6a)"></div>
  <div role="img" aria-label="Photo of a fluffy dog on a wooden floor" style="background:linear-gradient(#b8ab98,#7a5a3a)"></div>
  <div role="img" aria-label="Photo of a woman hugging a dog" style="background:linear-gradient(#6a4a3a,#2a2220)"></div>
  <div role="img" aria-label="Photo of a child with a small dog on a sofa" style="background:linear-gradient(#d8d0c6,#8a8070)"></div>
  <div role="img" aria-label="Photo of a pink flower near a dog" style="background:linear-gradient(#9a8a7a,#c04a7a)"></div>
  <div role="img" aria-label="Photo of a backyard lawn" style="background:linear-gradient(#4a5a4a,#5a7a4a)"></div>
  <div role="img" aria-label="Photo of a black and white cat in a sink" style="background:linear-gradient(#6a5a4a,#c9c2b8)"></div>
</section>

<h2 class="abs sec-title" style="top:2105px">Our Client Testimonial</h2>
<div class="abs sec-rule" style="top:2153px"></div>
<div class="abs quote-avatar" role="img" aria-label="Client portrait" style="left:99px;top:2198px"></div>
<div class="abs quote" style="left:210px;top:2198px"><p>There are many variations of passages of Lorem Ipsum available, but the majority have suffered alteration in some form, by injected humour, or randomised words which don't look even slightly believable.</p><div class="who"><b>John Doe</b><span>CEO, Company Name</span></div></div>
<div class="abs quote-avatar" role="img" aria-label="Client portrait" style="left:621px;top:2198px"></div>
<div class="abs quote" style="left:732px;top:2198px"><p>There are many variations of passages of Lorem Ipsum available, but the majority have suffered alteration in some form, by injected humour, or randomised words which don't look even slightly believable.</p><div class="who"><b>John Doe</b><span>CEO, Company Name</span></div></div>

<div class="abs sub-band"></div>
<svg class="abs sub-blue" width="680" height="101"><polygon points="0,0 585,0 669,101 0,101" fill="var(--blue)"/></svg>
<div class="abs sub-text">SUBSCRIBE<br><b>TO OUR NEWSLETTER</b></div>
<div class="abs sub-input">Enter Your Email Address</div>
<div class="abs sub-btn">Subscribe</div>

<footer class="abs footer"></footer>
<div class="abs fcol" style="left:97px"><h5>QUICK LINKS</h5><ul><li>photo gallery</li><li>about us</li><li>services</li><li>policies</li><li>Contact us</li></ul></div>
<div class="abs fcol" style="left:289px"><h5>RECENT POSTS</h5><ul><li>Finibus Bonorum</li><li>Randomised words</li><li>Anything embarrassing</li><li>Renaissance</li></ul></div>
<div class="abs fcol" style="left:495px"><h5>USEFUL TIPS</h5><ul><li>Finibus Bonorum</li><li>Randomised words</li><li>Anything embarrassing</li><li>Renaissance</li><li>Anything embarrassing</li></ul></div>
<div class="abs fcol plain" style="left:720px"><h5>WORKING HOURS</h5><ul><li>Monday - Friday 10AM - 10PM</li><li>Saturday 9AM - 8PM</li><li>Sunday 9AM - 6PM</li></ul></div>
<div class="abs fcol contact" style="left:934px"><h5>CONTACT US</h5><ul>
  <li><svg viewBox="0 0 12 12"><path d="M6 0a4 4 0 0 0-4 4c0 3 4 8 4 8s4-5 4-8a4 4 0 0 0-4-4z" fill="#bbb"/></svg>00 Latin words, combined</li>
  <li><svg viewBox="0 0 16 16"><path d="M4 1l3 3-2 2c1 2 3 4 5 5l2-2 3 3-2 3C7 15 1 9 1 3z" fill="#bbb"/></svg>5550142210 / 5550142211</li>
  <li><svg viewBox="0 0 16 16"><rect x="1" y="3" width="14" height="10" fill="none" stroke="#bbb" stroke-width="1.5"/><path d="M1 3l7 6 7-6" fill="none" stroke="#bbb" stroke-width="1.5"/></svg>hello@birchfordpawhaven.com</li>
</ul></div>
<div class="abs bottom">Copyrights@2016 Birchford Paw Haven , All rights reserved</div>
</body>
</html>
```